Letterhead Design for Law Firm

**Edit: I have added the photo of a bottom that I like.

------
We are looking for a re-design of our new letterhead. The letterhead is for a law firm and will be used for digital and traditionally printed correspondence.

Here are some suggestions:

- Please use colours are #8ec900 and simple black.
- Please do not use any type of "waves" at the bottom of the page. This is not in style at all.
- Please stay modern yet conservative.
- Please use font Segoe UI Light or similar if you can
- Avoid clipart or illustrations.
- Utilize ample white space in the layout so the design looks clean and information is easy to read at a glance. Don't overcrowd the letterhead.
- Make sure the letterhead design is consistent with our brand identity (see corvelith.ca)
-Please, no black headers or footers.

I am attaching my current letterhead and signature for your convenience.

Remember, the letterhead is an extension of our professional identity. We are a successful firm and trial lawyers who correspond with insurers, judges, lawyers, courts, clients, etc. Make it new, modern, attractive, yet powerful and conservative.

It needs to be easily printable. I would like the bleed removed in print so the black bar the bottom crosses the page (but the text is not near the edges)
Updates

Low design quality

Target Market(s)

Clients, Government Offices, Judiciary, Lawyers, Insurance Companies, Colleagues.

Industry/Entity Type

Law

Other font styles liked:
• Segoe UI LIght, Calibri Light,

Colors
00AB8E
00BBA5
67D7C9
C6EFE9
E9F9F6

Requirements
Must have
• Everything that is on the letterhead now.
Nice to have
• Cutting Edge design, yet conservative.
Should not have
• law firm cliche design, images,

```html
<!DOCTYPE html>
<html lang="en">
<head>
<meta charset="utf-8">
<title>Varnell Personal Injury Lawyers — Letterhead</title>
<link href="https://fonts.googleapis.com/css2?family=Open+Sans:wght@300;400;600;700&display=swap" rel="stylesheet">
<style>
  :root {
    --brand-green: #8ec900;
    --ink: #111111;
    --paper: #ffffff;
  }
  * { margin: 0; padding: 0; box-sizing: border-box; }
  html, body { width: 849px; height: 1200px; overflow: hidden; background: var(--paper); }
  .letterhead {
    position: relative;
    width: 849px;
    height: 1200px;
    background: var(--brand-green);
    font-family: "Open Sans", "Segoe UI", sans-serif;
    font-weight: 300;
    color: var(--ink);
    overflow: hidden;
  }
  .sheet {
    position: absolute;
    left: 0; top: 11px; right: 1px; bottom: 1px;
    background: var(--paper);
    border-top-left-radius: 97px 95px;
  }
  .practice-box {
    position: absolute;
    left: 509px; top: 0;
    width: 180px; height: 141px;
    background: var(--brand-green);
    border-bottom-right-radius: 32px;
    padding: 38px 0 0 13px;
    font-size: 12.3px;
    line-height: 16.2px;
    letter-spacing: -0.1px;
  }
  .practice-box .practice-title { font-weight: 700; }
  .practice-box ul { list-style: none; }
  .firm-name {
    position: absolute;
    left: 190px; top: 44px;
    width: 300px;
    text-align: center;
    font-weight: 300;
    color: var(--ink);
  }
  .firm-name .name {
    display: block;
    font-size: 62px;
    line-height: 68px;
    letter-spacing: 2px;
  }
  .firm-name .tagline {
    display: block;
    margin-top: 12px;
    font-size: 16px;
    letter-spacing: 1.2px;
  }
  .footer-rule {
    position: absolute;
    height: 1.5px;
    background: var(--brand-green);
  }
  .footer-rule.top { left: 106px; width: 605px; top: 1072px; }
  .footer-rule.bottom { left: 104px; width: 605px; top: 1155px; }
  .contact {
    position: absolute;
    display: flex;
    align-items: center;
    font-size: 12px;
    letter-spacing: -0.2px;
    white-space: nowrap;
  }
  .contact svg { fill: var(--brand-green); flex: none; }
  .contact .label { font-weight: 400; }
</style>
</head>
<body>
<div class="letterhead">
  <div class="sheet"></div>

  <aside class="practice-box">
    <p class="practice-title">Practice Restricted:</p>
    <ul>
      <li>Serious Personal Injury</li>
      <li>Wrongful Death Litigation</li>
      <li>Long-Term Disability Litigation</li>
      <li>Wrongful Dismissal Litigation</li>
      <li>Employee Terminations</li>
    </ul>
  </aside>

  <header class="firm-name">
    <span class="name">VARNELL</span>
    <span class="tagline">PERSONAL INJURY LAWYERS</span>
  </header>

  <div class="footer-rule top"></div>

  <div class="contact" style="left:160px; top:1104px;">
    <svg width="22" height="15" viewBox="0 0 22 15"><path d="M0 0h22v15H0z M2 1.5l9 7 9-7v1.2l-5.6 4.4L20 13.5v0L13.4 7.9 11 9.8 8.6 7.9 2 13.5 7.6 7.1 2 2.7z" fill-rule="evenodd"/></svg>
    <span style="margin-left:13px;">maren@corvelith.ca</span>
  </div>

  <div class="contact" style="left:322px; top:1101px;">
    <svg width="17" height="23" viewBox="0 0 17 23"><path d="M3 1c1-.8 2.2-.6 2.8.3l1.8 3c.5.9.2 1.8-.6 2.3l-1.4.9c.4 3.2 2.200 7 4.6 9.2l1.5-.8c.9-.4 1.8-.1 2.3.7l1.7 3c.5.9.2 1.9-.7 2.5-1.6 1-3.2 1.1-4.6.3C5.3 19.6 1.3 12 1 6.3.9 4.1 1.6 2.2 3 1z"/></svg>
    <span style="margin-left:9px;">905-555-0142</span>
  </div>

  <div class="contact" style="left:450px; top:1104px;">
    <svg width="24" height="19" viewBox="0 0 24 19"><path d="M5 0h14v8H5z M7 2v1h10V2z M7 4.5v1h10v-1z M1 9h2v7h18V9h2v10H1z M4 12h16v3H4z" fill-rule="evenodd"/></svg>
    <span style="margin-left:8px;">905-555-0187</span>
  </div>

  <div class="contact" style="left:569px; top:1103px;">
    <svg width="21" height="21" viewBox="0 0 21 21"><circle cx="10.5" cy="10.5" r="10"/><g stroke="#fff" stroke-width="1.2" fill="none"><ellipse cx="10.5" cy="10.5" rx="4.5" ry="10"/><path d="M10.5 0.5v20M0.5 10.5h20M2 5.5h17M2 15.5h17"/></g></svg>
    <span style="margin-left:8px;">www.corvelith.ca</span>
  </div>

  <div class="contact" style="left:164px; top:1133px;">
    <svg width="15" height="20" viewBox="0 0 15 20"><path d="M7.5 0A7.3 7.3 0 0 0 .2 7.3C.2 12.4 7.5 20 7.5 20s7.3-7.6 7.3-12.7A7.3 7.3 0 0 0 7.5 0zm0 4.3a3 3 0 1 1 0 6 3 3 0 0 1 0-6z"/></svg>
    <span style="margin-left:13px;">9 Kent Street W., Suite 1210 Hamilton, ON&nbsp;&nbsp;L8P 3K2</span>
  </div>

  <div class="contact" style="left:489px; top:1131px;">
    <svg width="18" height="22" viewBox="0 0 18 22"><circle cx="9" cy="5.5" r="5.5"/><path d="M0 22v-3.5C0 14.8 3 12.5 6 12.5l3 3 3-3c3 0 6 2.3 6 6V22z"/></svg>
    <span style="margin-left:7px;"><span class="label">File Clerk:</span> Maren Ashworth</span>
  </div>

  <div class="footer-rule bottom"></div>
</div>
</body>
</html>
```